Business Card Design

Electronic Security Installation Specialists

Check out our website at www.tallbrookllc.com to see what we do.

Industry/Entity Type

Business

Contact Information for Business Card

Tall Brook
Marjorie Hadley
281 Orchard Rise
Mapleton, WV 25871

Colors
3176b5
0455a3
ffffff

```html
<!DOCTYPE html>
<html lang="en">
<head>
<meta charset="utf-8">
<title>Tall Brook — Business Card</title>
<link rel="stylesheet" href="https://fonts.googleapis.com/css2?family=Open+Sans:wght@400;600;700&display=swap">
<style>
  :root {
    --brand-blue: #0455a3;
    --accent-blue: #3176b5;
    --card-white: #ffffff;
    --stage: #e9ebee;
    --ink: #3a3a3a;
    --ink-soft: #555b61;
    --faint: #eef1f4;
  }
  * { box-sizing: border-box; margin: 0; padding: 0; }
  html, body {
    width: 1200px; height: 913px; overflow: hidden;
    background: var(--stage);
    font-family: "Open Sans", Arial, sans-serif;
  }
  .stage { position: relative; width: 1200px; height: 913px; }
  .card {
    position: absolute;
    width: 525px; height: 300px;
    background: var(--card-white);
    box-shadow: 0 6px 18px rgba(0,0,0,.14);
    overflow: hidden;
  }
  .card--front { left: 50px; top: 130px; }
  .card--back { left: 625px; top: 480px; }

  .decor-arc {
    position: absolute; left: 60px; top: 20px;
    width: 420px; height: 260px;
    border-radius: 50%;
    background: radial-gradient(ellipse at center, transparent 58%, var(--faint) 60%, var(--faint) 66%, transparent 68%);
  }
  .brand {
    position: absolute;
    display: flex; align-items: center; gap: 12px;
  }
  .card--front .brand { left: 50%; top: 50%; transform: translate(-50%, -50%); }
  .card--back .brand { left: 38px; top: 50%; transform: translateY(-50%); }
  .brand__dot {
    width: 54px; height: 54px; border-radius: 50%;
    background: var(--brand-blue);
    flex: none;
  }
  .brand__name {
    font-weight: 700; font-size: 34px; color: var(--brand-blue);
    white-space: nowrap;
  }
  .card--back .brand__name { font-size: 28px; }
  .card--back .brand__dot { width: 46px; height: 46px; }

  .contact {
    position: absolute; left: 292px; top: 58px;
    color: var(--ink); font-size: 12px; line-height: 1.45;
  }
  .contact__name { font-weight: 700; font-size: 17px; color: var(--accent-blue); line-height: 1.2; }
  .contact__title { font-size: 12px; color: var(--ink-soft); margin-bottom: 30px; }
  .contact__address { margin-bottom: 8px; }
  .contact__line { display: flex; align-items: center; gap: 7px; }
  .contact__line svg { width: 11px; height: 11px; fill: var(--brand-blue); flex: none; }
  .contact__web { color: var(--accent-blue); }
</style>
</head>
<body>
<main class="stage">
  <section class="card card--front" aria-label="Card front">
    <div class="decor-arc" role="img" aria-label="Faint cable decoration"></div>
    <div class="brand">
      <span class="brand__dot"></span>
      <span class="brand__name">Tall Brook</span>
    </div>
  </section>

  <section class="card card--back" aria-label="Card back">
    <div class="brand">
      <span class="brand__dot"></span>
      <span class="brand__name">Tall Brook</span>
    </div>
    <div class="contact">
      <p class="contact__name">Marjorie Hadley</p>
      <p class="contact__title">Managing Director</p>
      <p class="contact__address">281 Orchard Rise<br>Mapleton, WV 25871</p>
      <p class="contact__line">
        <svg viewBox="0 0 24 24" aria-hidden="true"><path d="M6.6 10.8a15.1 15.1 0 0 0 6.6 6.6l2.2-2.2c.3-.3.7-.4 1-.2 1.1.4 2.3.6 3.6.6.6 0 1 .4 1 1V20c0 .6-.4 1-1 1C10.6 21 3 13.4 3 4c0-.6.4-1 1-1h3.5c.6 0 1 .4 1 1 0 1.3.2 2.5.6 3.6.1.3 0 .7-.2 1z"/></svg>
        304-555-0187
      </p>
      <p class="contact__line">
        <svg viewBox="0 0 24 24" aria-hidden="true"><path d="M2 5h20v14H2zm2 2v.5l8 5 8-5V7l-8 5z"/></svg>
        m.hadley@tallbrookllc.com
      </p>
      <p class="contact__line contact__web">
        <svg viewBox="0 0 24 24" aria-hidden="true"><path d="M12 2a10 10 0 1 0 0 20 10 10 0 0 0 0-20zm6.9 6h-3a15 15 0 0 0-1.3-3.9A8 8 0 0 1 18.9 8zM12 4c.8 1.2 1.5 2.5 1.9 4h-3.8c.4-1.5 1.1-2.8 1.9-4zM4.3 14a8 8 0 0 1 0-4h3.4a16 16 0 0 0 0 4zm.8 2h3a15 15 0 0 0 1.3 3.9A8 8 0 0 1 5.1 16zm3-8h-3a8 8 0 0 1 4.3-3.9A15 15 0 0 0 8.1 8zM12 20c-.8-1.2-1.5-2.5-1.9-4h3.8c-.4 1.5-1.1 2.8-1.9 4zm2.3-6H9.7a14 14 0 0 1 0-4h4.6a14 14 0 0 1 0 4zm.3 5.9a15 15 0 0 0 1.3-3.9h3a8 8 0 0 1-4.3 3.9zm1.7-5.9a16 16 0 0 0 0-4h3.4a8 8 0 0 1 0 4z"/></svg>
        www.tallbrookllc.com
      </p>
    </div>
  </section>
</main>
</body>
</html>
```